Help our Sugar Loom find our winning design! We're looking for a business card....

We’re a Sugar Loom in NY specializing in custom-made cakes and unique desserts.
Our cakes combine flavor and art, each designed to match customer’s special event and theme.
We’d like a unique business card with a clean design that will combine French chic and artistic look & feel.
We’d like to differentiate ourselves from standard bakeries, please don’t offer cupcake images :-)
Our logo is peach-pink and brown and we’d love to use these colors ( . Another color that can be added is gold - or feel free to suggest!

Target Market(s)

Women, ages 25-55

Industry/Entity Type

Boutique

Contact Information for Business Card

Text on card:
Logo
Sugar Loom by Dana Welch

www.sugarloomsweets.com
hello@sugarloom.com
(516) 555-0147
F – sugarloomnyc
IG - sugarloom_ny

Font styles to use
Sans Serif
Script

Requirements
Must have
• Logo
• Clean look
• French chic and artistic look & feel.
Nice to have
• Damask pattern
Should not have
• Cupcake images

```html
<!DOCTYPE html>
<html lang="en">
<head>
<meta charset="utf-8">
<title>Sugar Loom – Business Card</title>
<link href="https://fonts.googleapis.com/css2?family=Exo+2:wght@400;500;600&display=swap" rel="stylesheet">
<style>
  :root{
    --backdrop:#e4e6e8;
    --card-white:#ffffff;
    --slate:#6d6765;
    --blush:#ef8fa6;
    --ink:#2b2b2b;
    --logo-pink:#e58aa2;
  }
  *{margin:0;padding:0;box-sizing:border-box}
  html,body{width:1200px;height:864px;overflow:hidden;background:var(--backdrop)}
  body{display:flex;align-items:center;justify-content:center;font-family:"Exo 2",sans-serif}
  .card{position:relative;width:1000px;height:572px;background:var(--card-white);overflow:hidden;box-shadow:0 10px 30px rgba(0,0,0,.15)}
  .card-shapes{position:absolute;inset:0}
  .brand{position:absolute;top:70px;right:50px;text-align:right}
  .brand-name{font-size:40px;font-weight:500;color:var(--logo-pink);letter-spacing:1px}
  .address{position:absolute;top:160px;right:50px;text-align:right;font-size:22px;font-weight:600;color:var(--ink);line-height:1.35}
  .contact-list{position:absolute;top:250px;right:50px;list-style:none;text-align:right}
  .contact-list li{display:flex;align-items:center;justify-content:flex-end;gap:10px;font-size:17px;color:var(--ink);line-height:1;margin-bottom:14px}
  .contact-list svg{width:18px;height:18px;flex:none}
  .holder{position:absolute;left:70px;bottom:70px;color:#fff}
  .holder-name{font-size:30px;font-weight:500;letter-spacing:1.5px;text-transform:uppercase}
  .holder-title{font-size:20px;margin-top:6px;padding-left:40px}
</style>
</head>
<body>
<div class="card">
  <svg class="card-shapes" viewBox="0 0 1000 572" aria-hidden="true">
    <rect width="1000" height="572" fill="var(--slate)"/>
    <polygon points="560,572 700,390 1000,300 1000,572" fill="var(--card-white)"/>
    <ellipse cx="650" cy="150" rx="445" ry="250" fill="var(--blush)"/>
    <ellipse cx="672" cy="144" rx="428" ry="246" fill="var(--card-white)"/>
    <polygon points="230,0 1000,0 1000,320 700,390" fill="var(--card-white)" opacity="0"/>
  </svg>

  <div class="brand"><span class="brand-name">Sugar Loom</span></div>

  <div class="address">214 Mott Street<br>New York NY</div>

  <ul class="contact-list">
    <li>(516) 555-0147
      <svg viewBox="0 0 24 24"><path d="M6.6 10.8a15 15 0 0 0 6.6 6.6l2.2-2.2c.3-.3.7-.4 1-.2 1.1.4 2.3.6 3.6.6.6 0 1 .4 1 1V20c0 .6-.4 1-1 1A17 17 0 0 1 3 4c0-.6.4-1 1-1h3.5c.6 0 1 .4 1 1 0 1.3.2 2.5.6 3.6.1.3 0 .7-.2 1z" fill="var(--ink)"/></svg></li>
    <li>(516) 555-0182
      <svg viewBox="0 0 24 24"><rect x="6" y="2" width="12" height="20" rx="2" fill="none" stroke="var(--ink)" stroke-width="2"/><circle cx="12" cy="18" r="1.2" fill="var(--ink)"/></svg></li>
    <li>(516) 555-0193
      <svg viewBox="0 0 24 24"><rect x="3" y="9" width="18" height="11" rx="1.5" fill="var(--ink)"/><rect x="7" y="3" width="10" height="6" fill="none" stroke="var(--ink)" stroke-width="2"/></svg></li>
    <li>hello@sugarloom.com
      <svg viewBox="0 0 24 24"><rect x="2" y="5" width="20" height="14" rx="1.5" fill="var(--ink)"/><path d="M3 6l9 7 9-7" fill="none" stroke="#fff" stroke-width="1.6"/></svg></li>
    <li>www.sugarloomsweets.com
      <svg viewBox="0 0 24 24"><circle cx="12" cy="12" r="9.5" fill="none" stroke="var(--ink)" stroke-width="2"/><ellipse cx="12" cy="12" rx="4" ry="9.5" fill="none" stroke="var(--ink)" stroke-width="1.6"/><path d="M2.5 12h19M4.5 7h15M4.5 17h15" stroke="var(--ink)" stroke-width="1.4"/></svg></li>
  </ul>

  <div class="holder">
    <div class="holder-name">Dana Welch</div>
    <div class="holder-title">Managing Director</div>
  </div>
</div>
</body>
</html>
```